BrivoTerna. Lantern of the Steady Harvest. Business card

Professional business card for BrivoTerna (Lantern of the Steady Harvest)
My rationale: Strategy-> Execution-> Results-> Value that lead to the BrivoTerna name: We put the Lantern of the Steady Harvest.
We deliver value to our customers helping them at defining a good strategy (cyan arrow). 90% of well formulated strategies fail due to poor execution so we also consider strategical execution very important (green arrow). Due to the execution we obtain the results (blue arrow). Finally, the results provide feedback to redefine strategy, and the new strategy has to be executed and new results obtained providing new feedback and on and on. It's like a wheel that finally, must create corporate value: value for shareholders, staholders, employees, providers...-

Target Market(s)

CEOs and steering comitees , invewrnent funds

Industry/Entity Type

Business Consultant

Contact Information for Business Card

Teodoro Vinsquel
CEO & Founder
teodoro.vinsquel@brivoterna-example.com
Mobile: +34 655.803.912
www.brivoterna-example.com

Colors

Designer to choose colors to be used in the design.

Requirements
Nice to have
• Nice to hace the words: Strategy, execution, results
• Nice to vave the claim: Lantern of the Steady Harvest
• The three colors should be shown:
• cyan for STRATEGY
• green for EXECUTION
• blue for RESULTS
Should not have
• Complete black background

```html
<!DOCTYPE html>
<html lang="en">
<head>
<meta charset="utf-8">
<title>BrivoTerna — Business Card</title>
<link rel="stylesheet" href="https://fonts.googleapis.com/css2?family=Source+Sans+3:wght@400;600;700&display=swap">
<style>
  :root {
    --blue: #0a2f96;
    --green: #8cc63f;
    --cyan: #1cb3ea;
    --ink: #3a3a3a;
    --rule: #c9c9c9;
    --paper: #ffffff;
    --backdrop: #e6e7ea;
  }
  * { box-sizing: border-box; margin: 0; padding: 0; }
  html, body {
    width: 1200px; height: 900px; overflow: hidden;
    background: var(--backdrop);
    font-family: "Source Sans 3", "Myriad Pro", Arial, sans-serif;
  }
  .canvas { position: relative; width: 1200px; height: 900px; }

  .card {
    position: absolute;
    width: 640px; height: 366px;
    background: var(--paper);
    border-radius: 22px;
    overflow: hidden;
    box-shadow: 0 10px 28px rgba(0,0,0,0.18);
  }
  .card--front { left: 60px; top: 60px; }
  .card--back  { left: 500px; top: 474px; }

  .brand-name {
    position: absolute;
    color: var(--blue);
    font-weight: 700;
    letter-spacing: -1px;
    line-height: 1;
  }
  .card--front .brand-name { left: 42px; top: 96px; font-size: 58px; }
  .card--back .brand-name {
    left: 0; right: 0; top: 140px;
    text-align: center; font-size: 86px; letter-spacing: -2px;
  }

  .contact { position: absolute; left: 42px; top: 196px; width: 320px; }
  .contact__name { color: var(--blue); font-weight: 700; font-size: 19px; }
  .contact__title { color: var(--ink); font-size: 15px; margin-bottom: 8px; }
  .contact__line {
    display: flex; align-items: center; gap: 6px;
    color: var(--ink); font-size: 14.5px; line-height: 1.35;
  }
  .contact__line svg { width: 11px; height: 11px; flex: none; }
  .contact__web {
    margin-top: 8px; padding-top: 6px;
    border-top: 1px solid var(--rule);
    color: var(--ink); font-size: 16px; letter-spacing: 0.5px;
  }
  .contact__web strong { color: var(--blue); font-weight: 700; }

  .pillar-band {
    position: absolute; left: 0; right: 0; bottom: 0; height: 74px;
  }
  .pillar {
    position: absolute; bottom: 0;
    display: flex; align-items: flex-end;
    color: #fff; font-weight: 700; font-size: 17px; letter-spacing: 1px;
    padding: 0 0 7px 16px;
  }
  .pillar--strategy { left: 0; width: 150px; height: 34px; background: var(--cyan); }
  .pillar--execution { left: 150px; width: 150px; height: 40px; background: var(--green); }
  .pillar--results {
    left: 300px; right: 0; height: 66px; background: var(--blue);
    border-top: 5px solid var(--rule);
  }
</style>
</head>
<body>
<main class="canvas">

  <section class="card card--front" aria-label="Business card front">
    <div class="brand-name">BrivoTerna</div>

    <div class="contact">
      <p class="contact__name">Teodoro Vinsquel</p>
      <p class="contact__title">CEO &amp; Founder</p>
      <p class="contact__line">
        <svg viewBox="0 0 12 12" aria-hidden="true"><path d="M2.5 1 L4.5 1 L5.3 3.4 L4 4.5 Q5 7 7.5 8 L8.6 6.7 L11 7.5 L11 9.5 Q11 11 9.5 11 Q1 10 1 2.5 Q1 1 2.5 1 Z" fill="#0a2f96"/></svg>
        +34 655.803.912
      </p>
      <p class="contact__line">
        <svg viewBox="0 0 12 12" aria-hidden="true"><rect x="0.5" y="2" width="11" height="8" rx="1" fill="#0a2f96"/><path d="M1 2.6 L6 6.6 L11 2.6" stroke="#fff" stroke-width="1" fill="none"/></svg>
        teodoro.vinsquel@brivoterna-example.com
      </p>
      <p class="contact__web">www.<strong>brivoterna-example</strong>.com</p>
    </div>

    <div class="pillar-band">
      <div class="pillar pillar--strategy">STRATEGY</div>
      <div class="pillar pillar--execution">EXECUTION</div>
      <div class="pillar pillar--results">RESULTS</div>
    </div>
  </section>

  <section class="card card--back" aria-label="Business card back">
    <div class="brand-name">BrivoTerna</div>
  </section>

</main>
</body>
</html>
```